Business Card for Dental Office - "online review card"

I would like to develop a tasteful card (that would compliment my existing business card) that provides my patients a written link to a portal on my website that would facilitate the generation of online reviews.

My existing business card was a Lumaquarry project a few years ago and has been well received. I hope that it is easily accessed online for reference.

Target Market(s)

Existing patients who need guidance in accessing the "write a review" section of my website

Industry/Entity Type

Business

Requirements
Must have
• -a similar look to my existing card:
http://www.lumaquarry.com.au/contest.aspx?id=5192&page=3

-a link to the following url in writing:
http://www.tessaroldental.com/reviews.html

- a reference to "appreciating feedback" or "how are we doing?"

```html
<!DOCTYPE html>
<html lang="en">
<head>
<meta charset="utf-8">
<title>Online Review Card – Tessarol Dental</title>
<link rel="stylesheet" href="https://fonts.googleapis.com/css2?family=Montserrat:wght@300;400;500&family=Open+Sans:wght@700&family=Source+Sans+3:wght@400;600&display=swap">
<style>
  :root {
    --stage: #9a9a9a;
    --card: #ffffff;
    --card-edge: #3a3a3a;
    --navy: #2e3080;
    --navy-deep: #252660;
    --navy-light: #3a3d9a;
    --rule: #3a3a3a;
    --name-grey: #5a5a5a;
    --url-grey: #6b6b6b;
    --label: #ffffff;
    --watermark: #e6e6f2;
    --note-line: #7a7a7a;
  }
  * { margin: 0; padding: 0; box-sizing: border-box; }
  html, body { width: 1200px; height: 744px; overflow: hidden; }
  body {
    position: relative;
    background: var(--stage);
    font-family: "Source Sans 3", Arial, sans-serif;
  }
  .option-label {
    position: absolute;
    top: 29px;
    width: 200px;
    text-align: center;
    color: var(--label);
    font: 400 17px "Source Sans 3", Arial, sans-serif;
  }
  .card {
    position: absolute;
    width: 524px;
    height: 298px;
    background: var(--card);
    border: 1px solid var(--card-edge);
    border-radius: 10px;
    overflow: hidden;
  }
  .card--front-1 { left: 66px; top: 62px; }
  .card--front-2 { left: 624px; top: 62px; }
  .card--notes { left: 258px; top: 400px; }

  .side-band {
    position: absolute;
    left: 0; top: 0;
    width: 77px; height: 100%;
    background: linear-gradient(90deg, var(--navy-deep) 0%, var(--navy-light) 55%, var(--navy-deep) 100%);
  }
  .side-rule {
    position: absolute;
    left: 80px; top: 0;
    width: 3px; height: 100%;
    background: var(--rule);
  }
  .brand-tab {
    position: absolute;
    left: 23px; top: 22px;
    width: 90px; height: 103px;
    background: var(--card);
    border-radius: 12px;
  }
  .brand-square {
    position: absolute;
    left: 14px; top: 14px;
    width: 74px; height: 74px;
    background: var(--navy);
    border-radius: 10px;
  }
  .practice-name {
    position: absolute;
    left: 133px; top: 36px;
    font: 300 25px "Montserrat", Arial, sans-serif;
    color: var(--name-grey);
    white-space: nowrap;
  }
  .practice-name .credential { font-size: 16px; font-weight: 400; }
  .practice-sub {
    position: absolute;
    right: 120px; top: 68px;
    font: 500 9px "Montserrat", Arial, sans-serif;
    letter-spacing: 3.2px;
    color: var(--name-grey);
    white-space: nowrap;
  }
  .feedback-line {
    position: absolute;
    left: 91px; top: 146px;
    font: 600 17px "Source Sans 3", Arial, sans-serif;
    color: var(--navy);
    white-space: nowrap;
  }
  .review-url {
    position: absolute;
    left: 91px; top: 183px;
    font: 700 16px "Open Sans", Arial, sans-serif;
    white-space: nowrap;
  }
  .review-url--navy { color: var(--navy); }
  .review-url--grey { color: var(--url-grey); }
  .tagline {
    position: absolute;
    left: 91px; top: 235px;
    font: 400 18px "Source Sans 3", Arial, sans-serif;
    color: var(--navy);
    white-space: nowrap;
  }

  .notes-title {
    position: absolute;
    left: 0; top: 18px;
    width: 100%;
    text-align: center;
    font: 400 33px "Source Sans 3", Arial, sans-serif;
    color: var(--navy);
  }
  .notes-mark {
    position: absolute;
    left: 167px; top: 68px;
    width: 178px; height: 178px;
    background: var(--watermark);
    border-radius: 26px;
  }
  .notes-lines {
    position: absolute;
    left: 39px; top: 96px;
    width: 446px;
  }
  .notes-lines span {
    display: block;
    height: 33.6px;
    border-top: 1px solid var(--note-line);
  }
</style>
</head>
<body>
  <div class="option-label" style="left:238px">Option-1</div>
  <div class="option-label" style="left:780px">Option-2</div>

  <section class="card card--front-1">
    <div class="side-band"></div>
    <div class="side-rule"></div>
    <div class="brand-tab"><div class="brand-square"></div></div>
    <div class="practice-name">Martin E. Tessarol, <span class="credential">DDS</span></div>
    <div class="practice-sub">AND ASSOCIATES</div>
    <div class="feedback-line">HOW ARE WE DOING? WE APPRECIATE YOUR FEEDBACK</div>
    <div class="review-url review-url--navy">http://www.tessaroldental.com/reviews.html</div>
    <div class="tagline">STRIVING TO BE OUR BEST</div>
  </section>

  <section class="card card--front-2">
    <div class="side-band"></div>
    <div class="side-rule"></div>
    <div class="brand-tab"><div class="brand-square"></div></div>
    <div class="practice-name">Martin E. Tessarol, <span class="credential">DDS</span></div>
    <div class="practice-sub">AND ASSOCIATES</div>
    <div class="feedback-line">HOW ARE WE DOING? WE APPRECIATE YOUR FEEDBACK</div>
    <div class="review-url review-url--grey">http://www.tessaroldental.com/reviews.html</div>
    <div class="tagline">STRIVING TO BE OUR BEST</div>
  </section>

  <section class="card card--notes">
    <div class="notes-title">Notes</div>
    <div class="notes-mark"></div>
    <div class="notes-lines"><span></span><span></span><span></span><span></span><span></span><span></span></div>
  </section>
</body>
</html>
```